Coastal Learner Bureau business cards

Australian company about to start offering its services. We recruit international students to come to study English, vocational education and postgraduate courses in Australia. We help them find the institution and select the right city they want to come to Australia. We are a young, online oriented and supportive agency. Our clients are between 18 and 35 years old, mainly University students, young professionals or people with work experience. We provide much more information that any other agency offer. We administrate a Facebook group with more than 11.000 members that daily ask questions about general information when coming to Australia, while they are here and even after they leave the country

Target Market(s)

International students from South America, Central America and Europe

Industry/Entity Type

Student

Contact Information for Business Card

Tomas Bilbrea
Managing Director
tomas@kelvarin.com.au
www.kelvoria.com.au
+61 491058264
Melbourne, Australia

Font styles to use
Serif
Sans Serif

Colors

Designer to choose colors to be used in the design.

Requirements
Must have
• Horizontal design
• Standard business card size and shape. If font uses green or yellow colours, they will have to match the ones from the logo
Nice to have
• UPDATE: Use the contents of the green image to design one of the card sides. Use our logo in the background of that side as watermark.
• Passport image, or immigration stamps. A picture of the Yarra River (from Melbourne) would be cool as well.
Should not have
• Non-standard business card size and shape
• Not black as the background colour of any sides as we are not a VIP agency or a hight class service. We are orientes to young people and they like colours, pictures, something attractive.
• Vertical design
• NO YELLOW or BLACK AS THE BACKGROUND COLOUR OF ANY SIDE OF THE BIZ CARD

```html
<!DOCTYPE html>
<html lang="en">
<head>
<meta charset="utf-8">
<title>Coastal Learner Bureau – Business Cards</title>
<link href="https://fonts.googleapis.com/css2?family=Open+Sans:wght@400;700&display=swap" rel="stylesheet">
<style>
  :root {
    --page: #e9eae6;
    --card-white: #f7f7f5;
    --brand-green: #1a5c38;
    --brand-green-soft: #2a7049;
    --brand-yellow: #e2b619;
    --ink: #3b3b3b;
    --rule: #6f6f6f;
    --on-green: #ffffff;
  }
  * { margin: 0; padding: 0; box-sizing: border-box; }
  html, body {
    width: 1200px; height: 900px; overflow: hidden;
    background: var(--page);
    font-family: "Open Sans", Arial, sans-serif;
  }
  .sheet {
    width: 1200px; height: 900px;
    display: flex; flex-direction: column; align-items: center; justify-content: center;
    gap: 40px;
  }
  .card {
    width: 700px; height: 400px; position: relative; overflow: hidden;
    box-shadow: 0 6px 18px rgba(0,0,0,.18);
  }
  /* Front */
  .card--front { background: var(--card-white); }
  .brand {
    position: absolute; top: 120px; left: 0; right: 0;
    display: flex; align-items: center; justify-content: center; gap: 14px;
  }
  .brand__dot { width: 22px; height: 22px; border-radius: 50%; background: var(--brand-yellow); }
  .brand__name {
    font-weight: 700; font-size: 40px; color: var(--brand-green); letter-spacing: .5px;
  }
  .tagline {
    position: absolute; top: 268px; left: 40px; right: 40px;
    display: flex; align-items: center; gap: 12px;
  }
  .tagline__rule { flex: 1; height: 1px; background: var(--rule); }
  .tagline__text { font-size: 17px; font-weight: 700; color: var(--ink); white-space: nowrap; }
  /* Back */
  .card--back { background: var(--brand-green); }
  .map-area { position: absolute; inset: 0; }
  .contact {
    position: absolute; top: 120px; left: 0; right: 0;
    text-align: center; color: var(--on-green);
    font-size: 19px; line-height: 1.32;
  }
  .contact__name { font-weight: 700; text-transform: uppercase; }
  .contact__role { text-transform: uppercase; }
</style>
</head>
<body>
<main class="sheet">
  <section class="card card--front">
    <div class="brand">
      <span class="brand__dot"></span>
      <span class="brand__name">Coastal Learner Bureau</span>
    </div>
    <div class="tagline">
      <span class="tagline__rule"></span>
      <span class="tagline__text">Hacemos más por ti!</span>
      <span class="tagline__rule"></span>
    </div>
  </section>

  <section class="card card--back">
    <svg class="map-area" viewBox="0 0 700 400" role="img" aria-label="Large white outline map of Australia framing the contact details">
      <defs>
        <radialGradient id="mapGlow" cx="50%" cy="50%" r="55%">
          <stop offset="0" stop-color="var(--brand-green-soft)"/>
          <stop offset="1" stop-color="var(--brand-green)"/>
        </radialGradient>
      </defs>
      <rect x="110" y="30" width="480" height="340" rx="120" fill="url(#mapGlow)"/>
    </svg>
    <div class="contact">
      <p class="contact__name">Tomas Bilbrea</p>
      <p class="contact__role">Managing Director</p>
      <p>Melbourne, Australia</p>
      <p>+61 491058264</p>
      <p>tomas@kelvarin.com.au</p>
      <p>www.kelvoria.com.au</p>
    </div>
  </section>
</main>
</body>
</html>
```